Website for "Bright Morrow Ltd" cleaning bsuiness

We require a website to expose our business to the local market. We want to provide background on who we are and what we do but in an easily digestible way. We clean domestic and commercial premises and want to provide a list of all of our services to potential customers. We operate out of Warrington in the UK.

We would like the website to be animated in some way so that the experience of using it is not dull or mundane. This website needs to be an extension of our company.

Target Market(s)

30 - 60 year olds for Domestic plus commercial clients

Industry/Entity Type

Cleaning Service

Coding

Coded - Design and coding required

Number of Pages Required

4 page

Font styles to use
Sans Serif

Colors
0455a3
3176b5
85acd3
cfdeed
ffffff
000000
1b1b1b
c8c8c8
757575

Requirements
Must have
• Logo which has been provided. Theme based around the logo and its colours. Simple layout to avoid confusion.
Nice to have
• Animations where possible to impress the customer.
Should not have
• any pictures of cleaning equipment, fairies, maids etc

```html
<!DOCTYPE html>
<html lang="en">
<head>
<meta charset="utf-8">
<title>Bright Morrow Ltd – Professional Cleaning Service</title>
<link rel="stylesheet" href="https://fonts.googleapis.com/css2?family=Roboto:wght@300;400;500;700&family=Open+Sans:ital,wght@0,400;0,600;1,400&display=swap">
<style>
:root{
  --navy:#0455a3;
  --blue:#3176b5;
  --bright:#2b86e6;
  --sky:#85acd3;
  --mist:#cfdeed;
  --white:#ffffff;
  --black:#000000;
  --ink:#1b1b1b;
  --line:#c8c8c8;
  --grey:#757575;
  --paper:#eeeeee;
  --head:'Roboto',Arial,sans-serif;
  --body:'Open Sans',Arial,sans-serif;
}
*{box-sizing:border-box;margin:0;padding:0}
html,body{width:1200px;height:2899px;overflow:hidden}
body{font-family:var(--body);color:var(--grey);background:var(--white);position:relative}
.abs{position:absolute}
h2{font-family:var(--head);font-weight:400;font-size:23px;color:var(--ink);text-transform:uppercase;text-align:center;letter-spacing:.3px}
h2 span{color:var(--bright)}
.subtitle{font-family:var(--head);font-size:14px;color:var(--grey);text-align:center;text-transform:uppercase;letter-spacing:.3px}

/* header */
.topbar{top:0;left:0;width:1200px;height:93px;background:var(--white)}
.search{left:85px;top:31px;width:240px;height:39px;border:1px solid #e2e2e2;background:#f7f7f7;font-size:11px;color:#999;padding:11px 12px;text-transform:uppercase}
.search svg{position:absolute;right:12px;top:12px}
.social-top{right:85px;top:32px;display:flex;gap:9px}
.social-top i{display:block;width:35px;height:35px;border:1.5px solid #bcbcbc;border-radius:50%}
.navbar{top:93px;left:0;width:1200px;height:56px;background:linear-gradient(var(--navy),#04498d);display:flex;align-items:center}
.navbar a{position:absolute;color:var(--white);text-decoration:none;font-family:var(--head);font-size:13px;text-transform:uppercase;top:20px;transform:translateX(-50%)}
.brand-disc{left:518px;top:39px;width:162px;height:139px;border-radius:50%;background:var(--white);display:flex;flex-direction:column;align-items:center;justify-content:center;z-index:3}
.brand-name{font-family:var(--head);font-weight:700;color:var(--navy);font-size:21px;line-height:1.05;text-align:center}

/* hero */
.hero{top:149px;left:0;width:1200px;height:510px;background:linear-gradient(100deg,#8ea6bb 0%,#c3d1de 30%,#9fb6cb 55%,#6f8ba6 80%,#5a7692 100%)}
.hero-text{left:732px;top:190px;width:400px;color:var(--white)}
.hero-text h1{font-family:var(--head);font-weight:300;font-size:43px;letter-spacing:.5px;margin-bottom:14px}
.hero-text p{font-size:12px;line-height:24px}
.btn{display:inline-block;font-family:var(--head);font-size:14px;text-transform:uppercase;color:var(--white);text-align:center}
.hero .btn{position:absolute;left:732px;top:355px;width:147px;height:45px;line-height:45px;background:var(--navy);border-radius:2px}
.dots{left:1066px;top:632px;display:flex;gap:7px}
.dots i{width:10px;height:10px;border-radius:50%;background:var(--navy)}
.dots i.on{background:var(--white)}

/* welcome */
.welcome{top:659px;left:0;width:1200px;height:286px;background:var(--white)}
.welcome h2{position:absolute;top:56px;width:100%}
.welcome p{position:absolute;top:102px;left:210px;width:780px;font-size:11.5px;line-height:25px;text-align:center}
.welcome .btn{position:absolute;top:199px;height:38px;line-height:38px;border-radius:2px;font-weight:500}
.btn-dark{left:456px;width:139px;background:var(--navy)}
.btn-light{left:605px;width:139px;background:var(--bright)}

/* services */
.services{top:945px;left:0;width:1200px;height:527px;background:var(--paper)}
.services h2{position:absolute;top:28px;width:100%}
.services .subtitle{position:absolute;top:68px;width:100%}
.service{top:195px;width:247px;height:270px;color:var(--white);text-align:center}
.service.dark{background:var(--navy)}
.service.light{background:var(--bright)}
.service .photo{position:absolute;left:42px;top:-62px;width:163px;height:163px;border-radius:50%;border:4px solid var(--white);box-shadow:0 0 0 2px var(--navy)}
.service h3{position:absolute;top:128px;width:100%;font-family:var(--head);font-weight:500;font-size:15px;text-transform:uppercase}
.service p{position:absolute;top:158px;left:18px;width:211px;font-size:11.5px;line-height:22px}
.service a{position:absolute;top:233px;width:100%;left:0;color:var(--white);font-size:11px;font-weight:600;text-decoration:underline}

/* featured */
.featured{top:1472px;left:0;width:1200px;height:340px;background:linear-gradient(160deg,#5c9ee6 0%,#2f7fd6 45%,#1f68bd 100%);color:var(--white);text-align:center}
.featured h2{position:absolute;top:90px;width:100%;color:var(--white)}
.featured p{position:absolute;top:136px;left:220px;width:760px;font-size:11.5px;line-height:25px}
.featured .btn{position:absolute;left:479px;top:205px;width:242px;height:43px;line-height:41px;border:1.5px solid var(--white);font-size:13px}

/* blog */
.blog{top:1812px;left:0;width:1200px;height:520px;background:var(--white)}
.blog h2{position:absolute;top:34px;width:100%}
.blog .subtitle{position:absolute;top:72px;width:100%}
.blog-arrows{left:1058px;top:64px;display:flex;gap:3px}
.blog-arrows span{width:26px;height:26px;border:1.5px solid #999;border-radius:50%;display:flex;align-items:center;justify-content:center}
.post{top:118px;width:325px}
.post .thumb{width:325px;height:211px;border:5px solid var(--white);box-shadow:0 0 0 1px var(--line),0 6px 8px -4px rgba(0,0,0,.25)}
.post h3{margin-top:28px;font-family:var(--head);font-weight:500;font-size:14px;color:var(--ink);text-transform:uppercase}
.post .meta{margin-top:16px;font-size:10.5px;font-style:italic;color:var(--navy);display:flex;gap:10px;align-items:center}
.post .meta span{text-decoration:underline}
.post .meta b{color:var(--grey);font-weight:400;font-style:normal}
.post p{margin-top:12px;font-size:11.5px;line-height:23px}

/* testimonial */
.testimonial{top:2332px;left:0;width:1200px;height:255px;background:linear-gradient(120deg,#3a8ff0,#2a7fe0 50%,#2f86e6);color:var(--white)}
.testimonial .quote{position:absolute;left:176px;top:64px;width:545px;font-size:11.5px;line-height:22px}
.testimonial .qmark{position:absolute;font-family:Georgia,serif;font-size:30px;line-height:1}
.testimonial .name{position:absolute;left:176px;top:178px;font-family:var(--head);font-weight:500;font-size:14px;text-transform:uppercase}
.testimonial .date{position:absolute;left:176px;top:202px;font-size:11px}
.portrait{left:774px;top:27px;width:194px;height:194px;border-radius:50%;border:5px solid var(--white);background:radial-gradient(circle at 50% 45%,#e3c3a8,#9a6b4e 70%,#5a3c2c)}

/* footer */
.footer{top:2587px;left:0;width:1200px;height:312px;background:#2a2a2a;color:var(--white)}
.footer-brand{left:106px;top:62px;width:219px;font-family:var(--head);font-weight:700;font-size:30px;line-height:1.1}
.footer h4{position:absolute;top:48px;font-family:var(--head);font-weight:500;font-size:17px;text-transform:uppercase}
.contact-list{left:383px;top:95px;font-size:11px;line-height:1.3}
.contact-list li{list-style:none;display:flex;gap:10px;margin-bottom:16px}
.contact-list svg{flex:none}
.newsletter{left:624px;top:92px;width:230px;font-size:12px;line-height:21px}
.newsletter .field{margin-top:18px;height:33px;background:var(--white);color:#888;font-size:11px;padding:9px 14px}
.newsletter .sub{margin-top:10px;width:80px;height:27px;line-height:27px;background:var(--bright);font-size:9.5px;text-align:center;text-transform:uppercase;font-weight:600}
.follow{left:906px;top:95px;width:215px;font-size:11.5px;line-height:21px}
.follow .icons{margin-top:18px;display:flex;gap:8px}
.follow .icons i{width:37px;height:37px;border:1.5px solid var(--white);border-radius:50%}
.copyright{top:278px;width:100%;text-align:center;font-size:11px}
</style>
</head>
<body>

<header class="abs topbar">
  <div class="abs search">Search
    <svg width="13" height="13" viewBox="0 0 13 13"><circle cx="5.3" cy="5.3" r="4" fill="none" stroke="#666" stroke-width="1.6"/><line x1="8.3" y1="8.3" x2="12" y2="12" stroke="#666" stroke-width="1.8"/></svg>
  </div>
  <div class="abs social-top"><i></i><i></i><i></i><i></i><i></i></div>
</header>

<nav class="abs navbar">
  <a href="#" style="left:162px">Home</a>
  <a href="#" style="left:290px">About Us</a>
  <a href="#" style="left:428px">Services</a>
  <a href="#" style="left:758px">Featured</a>
  <a href="#" style="left:884px">Blog</a>
  <a href="#" style="left:1016px">Contact Us</a>
</nav>
<div class="abs brand-disc"><div class="brand-name">Bright Morrow<br>Ltd</div></div>

<section class="abs hero" role="img" aria-label="Glass office building entrance with steps and paved forecourt">
  <div class="abs hero-text">
    <h1>BRIGHT MORROW</h1>
    <p>Sed ut perspiciatis unde omnis iste natus error sit voluptatem accusan tium doloremque laudantium, totam rem aperiam, eaque ipsa quae a illo inventore veritatis et quasi architecto beatae</p>
  </div>
  <a class="btn" href="#">Read More</a>
  <div class="abs dots"><i></i><i class="on"></i><i></i></div>
</section>

<section class="abs welcome">
  <h2>Welcome to <span>Bright Morrow</span></h2>
  <p>Sed ut perspiciatis unde omnis iste natus error sit voluptatem accusantium doloremque laudantium, totam rem aperiam, eaque ipsa quae ab illo inventore veritatis et quasi architecto beatae vitae dicta sunt explicabo. Nemo enim ipsam voluptatem quia voluptas sit aspernatur aut odit aut fugit, sed quia consequuntur magni dolores eos qui ratione voluptatem sequi nesciunt.</p>
  <a class="btn btn-dark" href="#">Learn More</a>
  <a class="btn btn-light" href="#">Our Featured</a>
</section>

<section class="abs services">
  <h2>Our <span>Services</span></h2>
  <div class="subtitle">Neque porro quisquam est qui dolorem ipsum quia dolor sit amet</div>

  <div class="abs service dark" style="left:87px">
    <div class="photo" role="img" aria-label="Bright modern residential bathroom" style="background:radial-gradient(circle,#f2f5f8,#aebfd0)"></div>
    <h3>Residential Cleaning</h3>
    <p>Sed ut perspiciatis unde omnis iste nat us error sit voluptatem accusantium vitae itae dicta sunt explicabo.</p>
    <a href="#">READ MORE</a>
  </div>
  <div class="abs service light" style="left:346px">
    <div class="photo" role="img" aria-label="Commercial office interior with large windows" style="background:radial-gradient(circle,#f7f9fb,#c7d3de)"></div>
    <h3>Commercial Cleaning</h3>
    <p>Sed ut perspiciatis unde omnis iste nat us error sit voluptatem accusantium vitae itae dicta sunt explicabo.</p>
    <a href="#">READ MORE</a>
  </div>
  <div class="abs service dark" style="left:606px">
    <div class="photo" role="img" aria-label="Newly built high-rise apartment tower" style="background:linear-gradient(#8fb6e0,#e6e1d8 60%,#9c9386)"></div>
    <h3>Post Construction</h3>
    <p>Sed ut perspiciatis unde omnis iste nat us error sit voluptatem accusantium vitae itae dicta sunt explicabo.</p>
    <a href="#">READ MORE</a>
  </div>
  <div class="abs service light" style="left:866px">
    <div class="photo" role="img" aria-label="Glass building facade seen from below" style="background:linear-gradient(135deg,#dfe8ef,#7e97ad 50%,#cfdbe5)"></div>
    <h3>Clutter Cleanout</h3>
    <p>Sed ut perspiciatis unde omnis iste nat us error sit voluptatem accusantium vitae itae dicta sunt explicabo.</p>
    <a href="#">READ MORE</a>
  </div>
</section>

<section class="abs featured" role="img" aria-label="Blue tinted glass skyscrapers viewed from below">
  <h2>Our Featured</h2>
  <p>Sed ut perspiciatis unde omnis iste natus error sit voluptatem accusantium doloremque laudantium, totam rem aperiam, eaque ipsa quae odit aut fugit, sed quia consequuntur magni dolores eos qui ratione voluptatem sequi nesciunt.</p>
  <a class="btn" href="#">Click here for more info</a>
</section>

<section class="abs blog">
  <h2>Latest <span>Blog</span></h2>
  <div class="subtitle">Neque porro quisquam est qui dolorem ipsum quia dolor sit amet</div>
  <div class="abs blog-arrows">
    <span><svg width="8" height="10"><polyline points="6,1 2,5 6,9" fill="none" stroke="#777" stroke-width="1.6"/></svg></span>
    <span><svg width="8" height="10"><polyline points="2,1 6,5 2,9" fill="none" stroke="#777" stroke-width="1.6"/></svg></span>
  </div>

  <article class="abs post" style="left:87px">
    <div class="thumb" role="img" aria-label="Bright living room with white sofa and plant" style="background:linear-gradient(#f4f4f2 0%,#e3e3e0 55%,#c9c9c6 100%)"></div>
    <h3>Sed ut perspiciatis</h3>
    <div class="meta"><span>Clara Denton</span><b>|</b><span>20 Sep 2016</span><b>|</b><span>Comments (05)</span></div>
    <p>Sed ut perspiciatis unde omnis iste natus error sit volup tatem accusantium doloremque laudantium, totam et beatae vitae dicta sunt explicabo.</p>
  </article>
  <article class="abs post" style="left:435px">
    <div class="thumb" role="img" aria-label="Clean white kitchen counter" style="background:linear-gradient(#e9ecef 0%,#d6dbe0 50%,#f2f3f4 100%)"></div>
    <h3>Sed ut perspiciatis</h3>
    <div class="meta"><span>Clara Denton</span><b>|</b><span>20 Sep 2016</span><b>|</b><span>Comments (05)</span></div>
    <p>Sed ut perspiciatis unde omnis iste natus error sit volup tatem accusantium doloremque laudantium, totam et beatae vitae dicta sunt explicabo.</p>
  </article>
  <article class="abs post" style="left:783px">
    <div class="thumb" role="img" aria-label="Bright living room with white sofa and plant" style="background:linear-gradient(#f4f4f2 0%,#e3e3e0 55%,#c9c9c6 100%)"></div>
    <h3>Sed ut perspiciatis</h3>
    <div class="meta"><span>Clara Denton</span><b>|</b><span>20 Sep 2016</span><b>|</b><span>Comments (05)</span></div>
    <p>Sed ut perspiciatis unde omnis iste natus error sit volup tatem accusantium doloremque laudantium, totam et beatae vitae dicta sunt explicabo.</p>
  </article>
</section>

<section class="abs testimonial">
  <svg class="abs" style="left:48px;top:95px" width="16" height="60"><polyline points="14,2 2,30 14,58" fill="none" stroke="rgba(255,255,255,.5)" stroke-width="1.5"/></svg>
  <svg class="abs" style="left:1136px;top:95px" width="16" height="60"><polyline points="2,2 14,30 2,58" fill="none" stroke="rgba(255,255,255,.5)" stroke-width="1.5"/></svg>
  <span class="qmark" style="left:156px;top:42px">“</span>
  <p class="quote">Sed ut perspiciatis unde omnis iste natus error sit voluptatem accusantium doloremque laudantium, totam rem aperiam, eaque ipsa quae ab illo inventore veritatis et quasi architecto beatae vitae dicta sunt explicabo. Nemo enim ipsam voluptatem quia voluptas sit aspernatur aut odit aut fugit, sed quia consequuntur magni dolores eos qui ratione voluptatem sequi nesciunt.</p>
  <span class="qmark" style="left:612px;top:148px">”</span>
  <div class="name">Clara Denton</div>
  <div class="date">Posted On 07 July 2016</div>
  <div class="abs portrait" role="img" aria-label="Portrait of a smiling customer"></div>
</section>

<footer class="abs footer">
  <div class="abs footer-brand">Bright Morrow Ltd</div>

  <h4 style="left:383px">Contact Us</h4>
  <ul class="abs contact-list">
    <li><svg width="13" height="12" viewBox="0 0 13 12"><rect x="1" y="3" width="11" height="8" rx="1" fill="#fff"/><path d="M1 4 Q6.5-1 12 4" fill="none" stroke="#fff" stroke-width="1.5"/></svg>(000)-121-1231 &nbsp;(Phone)</li>
    <li><svg width="13" height="12" viewBox="0 0 13 12"><rect x="3" y="0" width="7" height="4" fill="#fff"/><rect x="0" y="4" width="13" height="5" rx="1" fill="#fff"/><rect x="3" y="8" width="7" height="4" fill="#fff"/></svg>(000)-121-1231 &nbsp;(Fax)</li>
    <li><svg width="13" height="10" viewBox="0 0 13 10"><rect x=".5" y=".5" width="12" height="9" fill="none" stroke="#fff"/><polyline points="1,1 6.5,6 12,1" fill="none" stroke="#fff"/></svg><span style="text-decoration:underline">info@brightmorrow.example</span></li>
    <li><svg width="13" height="14" viewBox="0 0 13 14"><path d="M6.5 13 C2 8 1.5 6.5 1.5 5 a5 5 0 0 1 10 0 c0 1.5-.5 3-5 8z" fill="#fff"/><circle cx="6.5" cy="5" r="1.8" fill="#2a2a2a"/></svg><span># 2564 Lorem Ipsum Dummy<br>Lorem Ipsum Dummy</span></li>
  </ul>

  <h4 style="left:624px">Newsletter</h4>
  <div class="abs newsletter">
    Register Your email address to get information about us
    <div class="field">Email Address</div>
    <div class="sub">Subscribe</div>
  </div>

  <h4 style="left:906px">Follow Us</h4>
  <div class="abs follow">
    Lorem ipsum dolor sit amet, conse ctetur adipiscing elit. Nulla in purus nibh. Donec ornare
    <div class="icons"><i></i><i></i><i></i><i></i><i></i></div>
  </div>

  <div class="abs copyright">© Copyright 2016 Bright Morrow. All Rights Reserved</div>
</footer>

</body>
</html>
```